Honey Company from Florida Needs Sweet and Buzz-worthy Site

Website Requests:
-Deluxe 5-Page Website with SSL-Secure Online Store (Shopify)
-High-end imagery to appeal to a discerning consumer
-Detailed verbiage with strong SEO and easy readability
-Design principles: simple, chic, luxe, earthy
Pages:
1. Home {Local, Raw American Honey from Florida}
2. The Hive
> About Us
>Meet the Beekeepers
3. Buy Honey
> Shopify retail store
4. The Buzz {News, Recipes & More}
> Blog
5. Contact Us {We're Buzzin' to Meet You}
> Store Hours
> Phone Number
> Address
> Quick Contact Form
Attachments: Web design notes, Logo, Color Codes, Inspiration Photos
Target Market(s)
High-end honey consumer in the U.S.
Industry/Entity Type
Upscale honey enthusiasts; direct to consumer sales.
Coding
Coded - Design and coding required
Number of Pages Required
5+ page
Requirements
Must have
- Upscale look and feel, easy usability for quick sales.

```html
<!DOCTYPE html>
<html lang="en">
<head>
<meta charset="utf-8">
<title>Amber Grove Company — Raw Florida Honey</title>
<link href="https://fonts.googleapis.com/css2?family=Noto+Serif:wght@300;400;500;600&family=Roboto:wght@400;500&display=swap" rel="stylesheet">
<style>
:root{
  --honey:#e9c350;
  --ink:#1c1a1d;
  --text:#222222;
  --muted:#3a3a3a;
  --paper:#ffffff;
  --field:#e8e9ea;
  --card-line:#e6e6e6;
}
*{margin:0;padding:0;box-sizing:border-box}
html,body{width:1200px;height:2844px;overflow:hidden;background:var(--paper)}
body{position:relative;font-family:"Noto Serif",Georgia,serif;color:var(--text)}
.abs{position:absolute}
.serif{font-family:"Noto Serif",Georgia,serif}
.sans{font-family:"Roboto",Arial,sans-serif}

.topbar{left:0;top:0;width:1200px;height:43px;background:var(--ink);color:var(--honey);font-size:12px;display:flex;align-items:center;justify-content:center}

.brand{left:550px;top:55px;width:100px;height:100px;border-radius:50%;border:2px solid var(--ink);display:flex;flex-direction:column;align-items:center;justify-content:center;text-align:center;color:var(--ink);font-weight:600;line-height:1.1}
.brand .big{font-size:17px}
.brand .small{font-size:10px;letter-spacing:.5px;margin-top:3px}
.icon{top:97px;width:16px;height:16px}

.main-nav{top:168px;left:0;width:1200px;display:flex;justify-content:center;gap:40px;font-size:13px;font-weight:500;letter-spacing:.3px;color:var(--ink)}
.footer-nav{top:2707px;color:#fff}

.hero-kicker{top:206px;width:1200px;text-align:center;color:var(--honey);font-size:35px;font-weight:400}
.hero-title{top:251px;width:1200px;text-align:center;color:var(--ink);font-size:35px;font-weight:400;line-height:45px}

.photo{display:block}
.watch{left:132px;top:818px;width:565px;height:53px;background:var(--honey);color:var(--ink);font-size:21px;padding-left:30px;display:flex;align-items:center}

.section-title{font-size:37px;font-weight:400;color:var(--ink);letter-spacing:.5px}
.rule{left:132px;top:996px;width:127px;height:3px;background:var(--honey)}

.card{top:1028px;width:298px;height:319px;border:1px solid var(--card-line);box-shadow:0 1px 4px rgba(0,0,0,.08);background:#fff;overflow:hidden}
.card svg{position:absolute;left:0;top:0}
.card-name{top:1362px;width:298px;text-align:center;font-size:25px;color:var(--ink);letter-spacing:1px}

.story{left:132px;top:1462px;width:468px;height:410px;background:var(--honey)}
.story h2{position:absolute;left:29px;top:44px;font-size:33px;font-weight:400;color:var(--ink)}
.story p{position:absolute;left:30px;top:98px;width:405px;font-size:13.4px;line-height:24px;font-weight:300;color:var(--ink)}
.pill{height:51px;width:158px;border-radius:26px;display:flex;align-items:center;justify-content:center;font-size:17px;letter-spacing:.5px}
.pill-light{background:#fff;color:var(--ink)}
.pill-honey{background:var(--honey);color:var(--muted)}

.feature-title{top:2178px;width:460px;text-align:center;font-size:18px;color:var(--ink);letter-spacing:.6px}
.feature-text{top:2215px;width:410px;text-align:center;font-size:13.4px;line-height:24px;font-weight:300;color:var(--muted)}

.footer{left:0;top:2436px;width:1200px;height:408px;background:var(--ink)}
.sub-title{top:2496px;width:1200px;text-align:center;font-size:34px;color:var(--honey)}
.sub-text{top:2550px;width:1200px;text-align:center;font-size:14px;color:#fff}
.email{left:369px;top:2595px;width:462px;height:50px;background:var(--field);display:flex;align-items:center;padding-left:15px;font-size:12px;color:var(--ink)}
.quick{top:2668px;width:1200px;text-align:center;font-size:15px;color:var(--honey)}
.divider{left:74px;top:2761px;width:1053px;height:1px;background:#8a8a8a}
.copyright{top:2785px;width:1200px;text-align:center;font-size:12.5px;color:#fff;letter-spacing:.3px}
.cards{left:984px;top:2783px;display:flex;gap:4px}
.cards span{width:31px;height:19px;background:#fff;border-radius:3px}
</style>
</head>
<body>

<div class="abs topbar serif">Lorem ipsum dolor sit amet, consectetur adipiscing elit, sed do eiusmod</div>

<svg class="abs icon" style="left:137px" viewBox="0 0 16 16" aria-label="Search"><circle cx="6.5" cy="6.5" r="4.5" fill="none" stroke="#1c1a1d" stroke-width="2.2"/><line x1="10" y1="10" x2="14" y2="14" stroke="#1c1a1d" stroke-width="2.6" stroke-linecap="round"/></svg>

<div class="abs brand serif"><span class="big">AMBER</span><span class="big">GROVE</span><span class="small">COMPANY</span></div>

<svg class="abs icon" style="left:977px" viewBox="0 0 16 16" aria-label="Account"><circle cx="8" cy="5" r="3.2" fill="#1c1a1d"/><path d="M2 15c0-4 2.6-6 6-6s6 2 6 6z" fill="#1c1a1d"/></svg>
<svg class="abs icon" style="left:1012px" viewBox="0 0 16 16" aria-label="Phone"><path d="M3 2l3 0 1.2 3.2-1.8 1.3c.8 1.8 2.2 3.2 4 4l1.3-1.8L14 10v3c0 .7-.6 1.2-1.3 1.1C7 13.6 2.4 9 1.9 3.3 1.8 2.6 2.3 2 3 2z" fill="#1c1a1d"/></svg>
<svg class="abs icon" style="left:1052px" viewBox="0 0 16 16" aria-label="Email"><rect x="1" y="3" width="14" height="10" rx="1" fill="#1c1a1d"/><path d="M1.5 4l6.5 5 6.5-5" fill="none" stroke="#fff" stroke-width="1.2"/></svg>

<nav class="abs main-nav sans"><span>HOME</span><span>THE HIVE</span><span>BUY HONEY</span><span>THE BUZZ</span><span>CONTACT</span></nav>

<h1 class="abs hero-kicker serif">BLESSED TO BEE-KEEP</h1>
<p class="abs hero-title serif">STRAIGHT FROM OUR BELOVED HIVES<br>TO YOUR LOVELY HOME</p>

<svg class="abs photo" style="left:132px;top:360px" width="565" height="458" role="img" aria-label="Honey jar wrapped in bee-print fabric beside an open gift box on a dark grey backdrop"><defs>
<linearGradient id="h1" x1="0" y1="0" x2="0" y2="1"><stop offset="0" stop-color="#3a3b3e"/><stop offset=".75" stop-color="#4d4e51"/><stop offset="1" stop-color="#6e6e70"/></linearGradient>
<radialGradient id="h1b" cx=".55" cy=".55" r=".45"><stop offset="0" stop-color="#e9dcc4" stop-opacity=".75"/><stop offset=".5" stop-color="#c9a86a" stop-opacity=".35"/><stop offset="1" stop-color="#4d4e51" stop-opacity="0"/></radialGradient>
</defs><rect width="565" height="458" fill="url(#h1)"/><rect width="565" height="458" fill="url(#h1b)"/></svg>
<div class="abs watch serif">WATCH VIDEO</div>

<svg class="abs photo" style="left:705px;top:360px" width="363" height="255" role="img" aria-label="Close-up of a honeybee on golden honeycomb"><defs>
<linearGradient id="h2" x1="0" y1="0" x2="1" y2="1"><stop offset="0" stop-color="#d7951a"/><stop offset=".5" stop-color="#f0b92e"/><stop offset="1" stop-color="#f7d66a"/></linearGradient>
<radialGradient id="h2b" cx=".65" cy=".45" r=".35"><stop offset="0" stop-color="#4a3214" stop-opacity=".55"/><stop offset="1" stop-color="#4a3214" stop-opacity="0"/></radialGradient>
</defs><rect width="363" height="255" fill="url(#h2)"/><rect width="363" height="255" fill="url(#h2b)"/></svg>
<svg class="abs photo" style="left:705px;top:625px" width="363" height="247" role="img" aria-label="Honeybees working across a frame of capped honeycomb"><defs>
<linearGradient id="h3" x1="0" y1="0" x2="1" y2="1"><stop offset="0" stop-color="#e0861a"/><stop offset=".45" stop-color="#f2a92a"/><stop offset="1" stop-color="#f8cf52"/></linearGradient>
<radialGradient id="h3b" cx=".3" cy=".6" r=".5"><stop offset="0" stop-color="#b5621a" stop-opacity=".45"/><stop offset="1" stop-color="#b5621a" stop-opacity="0"/></radialGradient>
</defs><rect width="363" height="247" fill="url(#h3)"/><rect width="363" height="247" fill="url(#h3b)"/></svg>

<h2 class="abs section-title serif" style="left:130px;top:938px">OUR PRODUCTS</h2>
<div class="abs rule"></div>

<div class="abs card" style="left:135px"><svg width="298" height="319" role="img" aria-label="Hexagonal honey jars in kraft packaging"><defs><radialGradient id="p1" cx=".5" cy=".5" r=".42"><stop offset="0" stop-color="#a9561a"/><stop offset=".45" stop-color="#c98b45"/><stop offset=".8" stop-color="#e9d6bd"/><stop offset="1" stop-color="#ffffff"/></radialGradient></defs><rect width="298" height="319" fill="url(#p1)"/></svg></div>
<div class="abs card" style="left:451px"><svg width="298" height="319" role="img" aria-label="Honey bottle in a wooden honeycomb frame box"><defs><radialGradient id="p2" cx=".5" cy=".5" r=".42"><stop offset="0" stop-color="#5c3a26"/><stop offset=".45" stop-color="#9a7150"/><stop offset=".8" stop-color="#e7d7c2"/><stop offset="1" stop-color="#ffffff"/></radialGradient></defs><rect width="298" height="319" fill="url(#p2)"/></svg></div>
<div class="abs card" style="left:767px"><svg width="298" height="319" role="img" aria-label="Gift set of three honey jars in a kraft box"><defs><radialGradient id="p3" cx=".5" cy=".5" r=".42"><stop offset="0" stop-color="#a7783f"/><stop offset=".45" stop-color="#ccaa77"/><stop offset=".8" stop-color="#efe3d1"/><stop offset="1" stop-color="#ffffff"/></radialGradient></defs><rect width="298" height="319" fill="url(#p3)"/></svg></div>

<div class="abs card-name serif" style="left:135px">PRODUCT NAME</div>
<div class="abs card-name serif" style="left:451px">PRODUCT NAME</div>
<div class="abs card-name serif" style="left:767px">PRODUCT NAME</div>

<section class="abs story">
  <h2 class="serif">AMBER GROVE</h2>
  <p class="serif">100% raw, unfiltered Florida honey straight from he beehives on his six-acre property, Amber Grove Honey Farm, 1480 Orchard Lane in Lakeview. Agricultural Company specializing in the Production of 100% Raw American Honey, and the Pollination of America’s food crops.Our Honey comes straight from our bee-hives to your table. No filtering, heating, or any funny stuff. Just All Natural, 100% Pure Florida Honey Natural Wild Honey- flavors include Orange Blossom, Gallberry, Summer Wildflower.</p>
  <div class="abs pill pill-light serif" style="left:30px;top:304px">LEARN MORE</div>
</section>
<svg class="abs photo" style="left:600px;top:1462px" width="468" height="410" role="img" aria-label="Black and gold honey gift boxes with glass jars and wooden spoons"><defs>
<linearGradient id="h4" x1="0" y1="0" x2="1" y2="1"><stop offset="0" stop-color="#1e1e22"/><stop offset=".55" stop-color="#26262a"/><stop offset="1" stop-color="#3a3220"/></linearGradient>
<radialGradient id="h4b" cx=".75" cy=".42" r=".3"><stop offset="0" stop-color="#e2b531" stop-opacity=".8"/><stop offset="1" stop-color="#e2b531" stop-opacity="0"/></radialGradient>
<radialGradient id="h4c" cx=".75" cy=".85" r=".25"><stop offset="0" stop-color="#d9a92a" stop-opacity=".7"/><stop offset="1" stop-color="#d9a92a" stop-opacity="0"/></radialGradient>
</defs><rect width="468" height="410" fill="url(#h4)"/><rect width="468" height="410" fill="url(#h4b)"/><rect width="468" height="410" fill="url(#h4c)"/></svg>

<svg class="abs photo" style="left:142px;top:1894px" width="448" height="266" role="img" aria-label="Honey dripping from a dipper into a jar beside honeycomb on wood"><defs>
<linearGradient id="h5" x1="0" y1="0" x2="0" y2="1"><stop offset="0" stop-color="#f4f1ec"/><stop offset=".55" stop-color="#e9d7bd"/><stop offset=".75" stop-color="#8a5a34"/><stop offset="1" stop-color="#5c3820"/></linearGradient>
<radialGradient id="h5b" cx=".35" cy=".55" r=".28"><stop offset="0" stop-color="#e8930f"/><stop offset="1" stop-color="#e8930f" stop-opacity="0"/></radialGradient>
<radialGradient id="h5c" cx=".72" cy=".72" r=".2"><stop offset="0" stop-color="#f4b53a"/><stop offset="1" stop-color="#f4b53a" stop-opacity="0"/></radialGradient>
</defs><rect width="448" height="266" fill="url(#h5)"/><rect width="448" height="266" fill="url(#h5b)"/><rect width="448" height="266" fill="url(#h5c)"/></svg>
<svg class="abs photo" style="left:609px;top:1894px" width="449" height="266" role="img" aria-label="Wooden honey dipper resting in a bowl of golden honey"><defs>
<radialGradient id="h6" cx=".55" cy=".55" r=".7"><stop offset="0" stop-color="#fbd24c"/><stop offset=".5" stop-color="#eda21c"/><stop offset="1" stop-color="#c7760c"/></radialGradient>
<radialGradient id="h6b" cx=".6" cy=".3" r=".25"><stop offset="0" stop-color="#8a3f10" stop-opacity=".55"/><stop offset="1" stop-color="#8a3f10" stop-opacity="0"/></radialGradient>
</defs><rect width="449" height="266" fill="url(#h6)"/><rect width="449" height="266" fill="url(#h6b)"/></svg>

<h3 class="abs feature-title serif" style="left:136px;font-weight:400">DON’T JUDGE A BEE BY ITS STINGER</h3>
<p class="abs feature-text serif" style="left:161px">If the bee disappeared off the face of the Earth, man would have only four years left to live.Hyper-efficient insects do play a vital role in agriculture. Almonds, for example, are almost entirely dependent on honeybee pollination.</p>
<div class="abs pill pill-honey serif" style="left:287px;top:2327px">LEARN MORE</div>

<h3 class="abs feature-title serif" style="left:604px;font-weight:400">REAL LOCAL HONEY, REALLY GOOD FOR YOU</h3>
<p class="abs feature-text serif" style="left:629px">Raw honey is loaded with antioxidants to protect your body from cell damage due to free radicals. Honey has been long known as a folk remedy to help heal burns and wounds due to its antibacterial and antifungal properties.</p>
<div class="abs pill pill-honey serif" style="left:755px;top:2327px">LEARN MORE</div>

<footer class="abs footer"></footer>
<h2 class="abs sub-title serif" style="font-weight:400">SUBSCRIBE TO OUR EMAILS</h2>
<p class="abs sub-text serif">Lorem ipsum dolor sit amet, consectetur adipiscing elit, sed do eiusmod</p>
<div class="abs email serif">Enter The Email</div>
<svg class="abs" style="left:792px;top:2612px" width="16" height="16" viewBox="0 0 16 16" aria-label="Send"><path d="M15 1L1 7l5 2 2 6z" fill="#1c1a1d"/></svg>
<div class="abs quick serif">QUICK LINKS</div>
<nav class="abs main-nav footer-nav sans"><span>HOME</span><span>THE HIVE</span><span>BUY HONEY</span><span>THE BUZZ</span><span>CONTACT</span></nav>
<div class="abs divider"></div>
<div class="abs copyright sans">© COPYRIGHTS 2021 AMBERGROVE &nbsp;|&nbsp; ALL RIGHTS RESERVED</div>
<div class="abs cards" aria-label="Accepted payment cards"><span></span><span></span><span></span><span></span></div>

</body>
</html>
```